Der Flyer soll das Format DIN 105 lang haben und später bei druckfalter.de gedruckt werden. Entsprechende Vorlagen sind bei druckfalter.de vorhanden. Der Flyer wird in der Mitte 1x gefalzt und beidseitige bedruckt. (Es gibt also eine Außenseite, eine Doppel Innenseiten und eine Rückseite)
Der Flyer soll Neupatienten sowie BEstandspatienten ansprechen und über die Ärzte und die Leistungen informieren. Siehe www.praxis-lindenhof-beispiel.de
Die Fotos auf der Homepage können verwendet werden, entsprechende Lizenzen für die Nutzung liegen vor. An besseren Ideen bin ich natürlich auch interessiert :-)
Datenübergabe in Adobe Illustrator (.ai) oder Adobe InDesign (.indd)
Vielen Dank und beste Grüße

```html
<!DOCTYPE html>
<html lang="en">
<head>
<meta charset="utf-8">
<title>Lindenhof Praxis – Flyer</title>
<link rel="stylesheet" href="https://fonts.googleapis.com/css2?family=Poppins:wght@400;500;600&display=swap">
<style>
  :root{
    --teal:#4cc2c0;
    --teal-dark:#2aa6a4;
    --teal-pale:#d9f1f0;
    --navy:#2d4e5c;
    --ink:#1f3a44;
    --grey-text:#4d5b61;
    --white:#ffffff;
    --stage:#eceeee;
    --sky:#6f9fd6;
    --sky-light:#c9dcef;
  }
  *{box-sizing:border-box;margin:0;padding:0}
  html,body{width:1200px;height:900px;overflow:hidden}
  body{background:var(--stage);font-family:"Poppins",Arial,sans-serif;color:var(--ink);position:relative}

  .flyer{position:absolute;left:195px;top:111px;width:812px;height:677px;display:flex}
  .panel{position:relative;height:677px;overflow:hidden}
  .panel--cover{width:405px;background:var(--white)}
  .panel--inside{width:407px;background:#f7f8f8}
  .panel-shapes{position:absolute;inset:0;width:100%;height:100%}

  .brand{position:absolute;display:flex;align-items:center;gap:7px;font-weight:500;font-size:14px}
  .brand-mark{width:12px;height:12px;background:var(--teal-dark)}
  .panel--cover .brand{left:28px;top:36px;color:var(--ink)}
  .panel--inside .brand{left:32px;top:36px;color:var(--white)}
  .panel--inside .brand-mark{background:var(--white)}

  .cover-headline{position:absolute;left:30px;top:456px;color:var(--white);font-weight:500;font-size:30px;line-height:40px}
  .cover-intro{position:absolute;left:28px;top:556px;width:300px;color:var(--white);font-size:12px;line-height:17px}

  .inside-title{position:absolute;left:32px;top:98px;color:var(--white);font-weight:500;font-size:25px;line-height:31px}
  .inside-subtitle{position:absolute;left:32px;top:167px;color:var(--white);font-size:12px;line-height:16px}

  .services-heading{position:absolute;left:32px;top:322px;color:var(--teal-dark);font-weight:500;font-size:20px;line-height:24px}
  .services-heading span{display:block;font-weight:400;font-size:17px}

  .service{position:absolute;width:170px;display:flex;gap:10px}
  .service-icon{flex:none;width:36px;height:36px;border-radius:50%}
  .service-icon--avatar{background:var(--teal)}
  .service-icon--line{border:2px solid var(--teal);background:transparent;width:28px;height:28px;margin:4px}
  .service-name{color:var(--teal-dark);font-weight:600;font-size:11px;line-height:15px}
  .service-lead{color:var(--ink);font-weight:600;font-size:10px;line-height:14px}
  .service-text{color:var(--grey-text);font-size:10px;line-height:14px}
</style>
</head>
<body>
<main class="flyer">

  <section class="panel panel--cover">
    <svg class="panel-shapes" viewBox="0 0 405 677" preserveAspectRatio="none" aria-hidden="false">
      <defs>
        <linearGradient id="buildingTones" x1="0" y1="0" x2="0" y2="1">
          <stop offset="0" stop-color="#5f8fcc"/>
          <stop offset="0.45" stop-color="#c9dcef"/>
          <stop offset="0.8" stop-color="#b9bec2"/>
          <stop offset="1" stop-color="#8e9599"/>
        </linearGradient>
      </defs>
      <path d="M0 140 C90 110 190 110 250 40 L260 190 L0 210 Z" fill="var(--teal-pale)"/>
      <path role="img" aria-label="Photo of the modern practice building under a blue sky"
            d="M0 165 C90 125 200 120 245 0 L405 0 L405 360 C300 400 150 420 0 395 Z" fill="url(#buildingTones)"/>
      <path d="M260 390 C320 340 360 290 405 250 L405 677 L260 677 Z" fill="var(--navy)"/>
      <path d="M0 395 C110 420 230 430 320 400 C355 390 380 410 390 460 C400 500 405 530 405 560 L405 677 L0 677 Z" fill="var(--teal)"/>
    </svg>
    <div class="brand"><span class="brand-mark"></span>Lindenhof Praxis</div>
    <h1 class="cover-headline">Your health<br>in good hands</h1>
    <p class="cover-intro">Personal care for new and long-time patients. Doctors, services and hours in one place for you.</p>
  </section>

  <section class="panel panel--inside">
    <svg class="panel-shapes" viewBox="0 0 407 677" preserveAspectRatio="none">
      <defs>
        <linearGradient id="doctorTones" x1="0" y1="0" x2="1" y2="1">
          <stop offset="0" stop-color="#e6ebee"/>
          <stop offset="0.6" stop-color="#f4f6f7"/>
          <stop offset="1" stop-color="#8fb4d4"/>
        </linearGradient>
      </defs>
      <rect role="img" aria-label="Photo of a smiling doctor in a white coat with a stethoscope"
            x="190" y="0" width="217" height="300" fill="url(#doctorTones)"/>
      <path d="M0 0 H250 C195 50 195 140 230 200 C265 260 235 305 140 300 C70 296 25 285 0 270 Z" fill="var(--teal)"/>
      <path d="M140 300 C230 300 300 285 340 260 C375 238 395 232 407 226 L407 290 C340 298 250 305 140 300 Z" fill="var(--navy)"/>
    </svg>
    <div class="brand"><span class="brand-mark"></span>Lindenhof Praxis</div>
    <h2 class="inside-title">Family<br>Practice</h2>
    <p class="inside-subtitle">Care for all ages<br>Close to your home<br>Open to new patients</p>

    <h3 class="services-heading">Services<span>at a glance</span></h3>

    <div class="service" style="left:32px;top:392px">
      <span class="service-icon service-icon--avatar" role="img" aria-label="Doctor portrait"></span>
      <div><p class="service-name">Checkups</p><p class="service-lead">Annual exams</p><p class="service-text">Routine health<br>screening visits</p></div>
    </div>
    <div class="service" style="left:208px;top:392px">
      <span class="service-icon service-icon--avatar" role="img" aria-label="Doctor portrait"></span>
      <div><p class="service-name">Our team</p><p class="service-lead">Meet the doctors</p><p class="service-text">Experienced family<br>medicine staff</p></div>
    </div>
    <div class="service" style="left:32px;top:472px">
      <span class="service-icon service-icon--line"></span>
      <div><p class="service-name">Heart</p><p class="service-lead">Cardio diagnostics</p><p class="service-text">ECG and blood<br>pressure tests</p></div>
    </div>
    <div class="service" style="left:208px;top:472px">
      <span class="service-icon service-icon--line"></span>
      <div><p class="service-name">Lab tests</p><p class="service-lead">Blood analysis</p><p class="service-text">Results fast and<br>clearly explained</p></div>
    </div>
    <div class="service" style="left:32px;top:562px">
      <span class="service-icon service-icon--line"></span>
      <div><p class="service-name">Vaccines</p><p class="service-lead">Travel advice</p><p class="service-text">All ages</p></div>
    </div>
    <div class="service" style="left:208px;top:562px">
      <span class="service-icon service-icon--line"></span>
      <div><p class="service-name">Home visits</p><p class="service-lead">Care at home</p><p class="service-text">When needed</p></div>
    </div>
  </section>

</main>
</body>
</html>
```